E learning Platform for privacy

Current website is as below and its more of a shell.
I need someone to take the text and content and design it properly.
https://study.vornaquill.com/

After that, design has to be implemented with elementor and wordpress
https://elementor.com/

```html
<!DOCTYPE html>
<html lang="en">
<head>
<meta charset="utf-8">
<title>Vornaquill Learning Centre</title>
<link href="https://fonts.googleapis.com/css2?family=Roboto:ital,wght@0,400;0,500;0,700;0,900;1,400&display=swap" rel="stylesheet">
<style>
:root{
  --orange:#e8601c;
  --orange-deep:#d9441c;
  --orange-light:#ef8a22;
  --ink:#222428;
  --text:#3a3a3a;
  --muted:#666;
  --line:#dedede;
  --paper:#ffffff;
  --mist:#f2f2f2;
  --footer:#25272c;
  --footer-text:#c9cacc;
}
*{margin:0;padding:0;box-sizing:border-box}
html,body{width:1200px;height:4386px;overflow:hidden}
body{position:relative;font-family:"Roboto",Arial,sans-serif;color:var(--text);background:var(--paper)}
.abs{position:absolute}
.btn{position:absolute;display:flex;align-items:center;justify-content:center;border-radius:30px;font-weight:700;font-size:14px;letter-spacing:.3px;text-transform:uppercase}
.btn-solid{background:var(--orange);color:#fff}
.btn-ghost{border:2px solid #fff;color:#fff}
.center{text-align:center;left:0;width:1200px}

/* header */
.site-header{position:absolute;top:0;left:0;width:1200px;height:82px;background:#fff}
.brand{position:absolute;left:172px;top:22px;display:flex;align-items:center;gap:10px;font-size:30px;font-weight:700;color:var(--orange)}
.brand-mark{width:14px;height:14px;background:var(--orange)}
.nav a{position:absolute;top:33px;font-size:12.5px;font-weight:500;color:#333;text-decoration:none;letter-spacing:.4px}
.nav a.active{color:var(--orange);border-bottom:2px solid var(--orange);padding-bottom:4px}
.nav .register{top:26px;left:928px;width:98px;height:29px;font-size:12px}

/* hero */
.hero{position:absolute;top:82px;left:0;width:1200px;height:680px;overflow:hidden}
.hero-photo{position:absolute;inset:0;background:linear-gradient(100deg,#2a2c2f 0%,#4a4744 30%,#8a6a55 55%,#c2561e 75%,#a34418 100%)}
.hero h1{position:absolute;left:172px;top:196px;font-size:57px;line-height:66px;font-weight:900;color:#fff;letter-spacing:.5px}
.hero .btn{left:175px;top:349px;width:170px;height:47px}
.dots{position:absolute;left:566px;top:578px;display:flex;gap:6px}
.dots span{width:12px;height:12px;border-radius:50%;background:#fff}
.dots span.on{background:var(--orange)}

/* stats */
.stat{position:absolute;top:829px;width:200px;text-align:center}
.stat-icon{width:60px;height:62px;margin:0 auto;border:3px solid var(--orange);border-radius:10px;opacity:.8}
.stat-num{margin-top:30px;font-size:29px;font-weight:700;color:var(--orange)}
.stat-label{margin-top:12px;font-size:13px;font-weight:500;letter-spacing:.8px;color:#222}
.divider{position:absolute;left:264px;top:1028px;width:672px;height:1px;background:var(--line)}

.section-title{position:absolute;font-size:35px;font-weight:500;color:var(--ink)}
.section-sub{position:absolute;font-size:13px;line-height:21px;color:#444}

/* courses */
.course{position:absolute;top:1202px;width:265px;height:422px;background:#fff;box-shadow:0 1px 6px rgba(0,0,0,.18)}
.course-art{height:199px;background:radial-gradient(circle at 50% 55%,#3b3f4a 0%,#24262b 60%)}
.badge{position:absolute;top:0;left:0;background:var(--orange);color:#fff;font-size:13px;font-weight:700;padding:5px 11px}
.course h3{margin:35px 16px 0;font-size:17.5px;line-height:25px;font-weight:500;color:#222}
.course p{margin:14px 16px 0;font-size:11px;line-height:21px;color:#333}
.course .dur{margin:10px 16px 0;font-size:12.5px;font-weight:500;color:var(--orange)}

/* why */
.why-title{position:absolute;left:172px;top:1826px;font-size:35px;line-height:43px;font-weight:500;color:#fff}
.why-intro{position:absolute;left:172px;top:1926px;width:375px;font-size:13px;line-height:23px;color:#fff}
.why-btn{left:172px;top:2039px;width:150px;height:44px}
.feature{position:absolute;width:201px;height:228px;background:#fff;text-align:center;padding:0 14px;box-shadow:0 2px 8px rgba(0,0,0,.12)}
.feature-icon{width:52px;height:52px;margin:28px auto 0;border:2.5px solid var(--orange);border-radius:50%}
.feature h4{margin-top:16px;font-size:15px;line-height:21px;font-weight:400;color:#333}
.feature-text{margin-top:14px;font-size:10.5px;line-height:18px;color:#555}

/* testimonials */
.quote{position:absolute;width:272px;height:213px;background:#fff;border:1px solid #e1e1e1;padding:26px 18px 0}
.quote.lift{box-shadow:0 4px 14px rgba(0,0,0,.14)}
.quote p{font-size:12px;line-height:21px;font-style:italic;color:#555}
.quote .who{margin-top:10px;font-size:13px;font-weight:500;color:#222}
.quote .who span{color:var(--orange);font-size:10px;letter-spacing:1px;margin-left:8px}
.quote .mark{position:absolute;right:22px;bottom:14px;font-size:60px;line-height:40px;color:#ddd;font-family:Georgia,serif}
.quote .tail{position:absolute;left:14px;bottom:-13px;width:0;height:0;border-left:13px solid transparent;border-right:13px solid transparent;border-top:13px solid #fff}
.arrow{position:absolute;top:2655px}

/* blog */
.post{position:absolute;top:3116px;width:265px}
.post-img{height:198px}
.date{display:inline-block;margin-top:17px;background:var(--orange);color:#fff;font-size:11px;font-weight:700;padding:4px 6px}
.post h3{margin-top:20px;font-size:17.5px;line-height:25px;font-weight:500;color:#222}
.post p{margin-top:12px;font-size:11px;line-height:21px;color:#333}

/* newsletter */
.news h2{position:absolute;font-size:35px;font-weight:500;color:#fff}
.news p{position:absolute;font-size:13px;line-height:21px;color:#fff}
.email{position:absolute;left:361px;top:3904px;width:478px;height:43px;border-radius:25px;background:#fff;padding:0 0 0 24px;display:flex;align-items:center;font-size:12px;color:#555}
.email .go{position:absolute;right:6px;top:6px;width:31px;height:31px;border-radius:50%;background:var(--orange)}

/* footer */
.footer{position:absolute;top:4071px;left:0;width:1200px;height:315px;background:var(--footer)}
.fcol{position:absolute;top:55px}
.fcol h5{font-size:13.5px;font-weight:700;color:#fff;margin-bottom:18px}
.fcol li{list-style:none;font-size:10.5px;line-height:23px;color:var(--footer-text)}
.contact-row{display:flex;gap:12px;margin-bottom:10px;font-size:10.5px;line-height:16px;color:var(--footer-text)}
.contact-row svg{flex:none;margin-top:4px}
.fbar{position:absolute;left:0;top:252px;width:1200px;height:1px;background:#3a3c41}
.copyright{position:absolute;left:180px;top:282px;font-size:10.5px;color:var(--footer-text)}
.powered{position:absolute;left:512px;top:280px;font-size:9px;color:#888;display:flex;gap:12px;align-items:center}
.powered b{font-size:13px;color:var(--orange)}
.powered i{font-style:normal;font-size:11px;color:#6f8fb0}
.social{position:absolute;left:885px;top:282px;display:flex;gap:19px}
.social span{width:14px;height:14px;border-radius:3px;background:#fff}
.chat{position:absolute;left:1082px;top:4298px;width:46px;height:46px;border-radius:50%;background:#2f7be0;display:flex;align-items:center;justify-content:center}
</style>
</head>
<body>

<header class="site-header">
  <div class="brand"><span class="brand-mark"></span>Vornaquill</div>
  <nav class="nav">
    <a class="active" style="left:383px">HOME</a>
    <a style="left:458px">BLOGS</a>
    <a style="left:537px">COURSES</a>
    <a style="left:637px">CONTACT US</a>
    <a style="left:755px">ABOUT US</a>
    <a style="left:856px">SIGN IN</a>
    <span class="btn btn-solid register">Register</span>
  </nav>
</header>

<section class="hero">
  <div class="hero-photo" role="img" aria-label="Photo of a woman in an orange shirt working on a laptop"></div>
  <svg class="abs" style="left:0;top:0" width="1200" height="680" viewBox="0 0 1200 680">
    <polygon points="0,618 760,640 0,664" fill="#e8601c"/>
    <polygon points="0,664 1200,642 1200,680 0,680" fill="#fff"/>
  </svg>
  <h1>PRIVACY PRACTICE<br>MASTERY</h1>
  <span class="btn btn-solid">Get Trained</span>
  <div class="dots"><span></span><span></span><span class="on"></span><span></span></div>
</section>

<section class="stats">
  <div class="stat" style="left:314px"><div class="stat-icon" role="img" aria-label="Graduate icon"></div><div class="stat-num">6,375</div><div class="stat-label">ENROLLED STUDENTS</div></div>
  <div class="stat" style="left:500px"><div class="stat-icon" role="img" aria-label="Lessons book icon"></div><div class="stat-num">114</div><div class="stat-label">OUR LESSONS</div></div>
  <div class="stat" style="left:656px"><div class="stat-icon" role="img" aria-label="Video icon"></div><div class="stat-num">169</div><div class="stat-label">VIDEOS</div></div>
</section>
<div class="divider"></div>

<section class="courses">
  <h2 class="section-title center abs" style="top:1062px">Featured Courses</h2>
  <p class="section-sub center" style="top:1117px">Sed ut perspiciatis unde omnise natus errort voluptatem accustiu<br>mdoloremque laedut perspictis unde omnis iste natu.</p>
  <article class="course" style="left:172px">
    <div class="course-art" role="img" aria-label="Course illustration: online learning on a computer"></div>
    <span class="badge">FREE</span>
    <h3>Neueorro uisuamloremst ui dolorem isumuiaolor</h3>
    <p>Lorem ipsum dolor sit amet, consecteis cing elit, sed do eiusmod tempor incidint ut labore et dolore magna aliquaeniami nim veniam,uis nostrud exercitore</p>
    <div class="dur">Duration: 55 Weeks</div>
  </article>
  <article class="course" style="left:466px">
    <div class="course-art" role="img" aria-label="Course illustration: dashboard on a laptop"></div>
    <span class="badge">FREE</span>
    <h3>Neueorro uisuamloremst ui dolorem isumuiaolor</h3>
    <p>Lorem ipsum dolor sit amet, consecteis cing elit, sed do eiusmod tempor incidint ut labore et dolore magna aliquaeniami nim veniam,uis nostrud exercitore</p>
    <div class="dur">Duration: 55 Weeks</div>
  </article>
  <article class="course" style="left:761px">
    <div class="course-art" role="img" aria-label="Course illustration: video lesson on a laptop"></div>
    <span class="badge">FREE</span>
    <h3>Neueorro uisuamloremst ui dolorem isumuiaolor</h3>
    <p>Lorem ipsum dolor sit amet, consecteis cing elit, sed do eiusmod tempor incidint ut labore et dolore magna aliquaeniami nim veniam,uis nostrud exercitore</p>
    <div class="dur">Duration: 55 Weeks</div>
  </article>
</section>

<section class="why">
  <svg class="abs" style="left:0;top:1700px" width="1200" height="770" viewBox="0 0 1200 770">
    <defs><linearGradient id="whyGrad" x1="0" y1="0" x2="1" y2="0"><stop offset="0" stop-color="#d9441c"/><stop offset="1" stop-color="#ec7d1e"/></linearGradient></defs>
    <polygon points="0,43 1200,7 1200,32 0,70" fill="#cfcfcf"/>
    <polygon points="0,70 1200,7 1200,720 0,763" fill="url(#whyGrad)"/>
    <polygon points="0,763 1200,720 1200,745 0,770" fill="#cfcfcf"/>
  </svg>
  <h2 class="why-title">Why the (Vornaquill)<br>Learning Centre?</h2>
  <p class="why-intro">Our mission at the Vornaquill Learning Centre is to provide business and job opportunities, as well as to enhance personal and career advancement for data protection / privacy professionals.</p>
  <span class="btn btn-ghost why-btn">Learn More</span>

  <div class="feature" style="left:608px;top:1838px"><div class="feature-icon" role="img" aria-label="Roadmap icon"></div><h4>Comprehensive<br>Roadmap</h4><p class="feature-text">Our objective is to provide a comprehensive competency roadmap, instead of one.</p></div>
  <div class="feature" style="left:826px;top:1816px"><div class="feature-icon" role="img" aria-label="Operational perspective icon"></div><h4>Operational<br>Perspective</h4><p class="feature-text">Our objective is to provide a comprehensive competency roadmap, instead of one.</p></div>
  <div class="feature" style="left:172px;top:2133px"><div class="feature-icon" role="img" aria-label="Certificate icon"></div><h4>Academic &amp; International<br>Certification</h4><p class="feature-text">Our objective is to provide a comprehensive competency roadmap, instead of one.</p></div>
  <div class="feature" style="left:390px;top:2110px"><div class="feature-icon" role="img" aria-label="Schedule icon"></div><h4>Modular Approach<br>&amp; Flexibility</h4><p class="feature-text">Our objective is to provide a comprehensive competency roadmap, instead of one.</p></div>
  <div class="feature" style="left:608px;top:2088px"><div class="feature-icon" role="img" aria-label="Network icon"></div><h4>Network with<br>other peers</h4><p class="feature-text">Our objective is to provide a comprehensive competency roadmap, instead of one.</p></div>
  <div class="feature" style="left:826px;top:2065px"><div class="feature-icon" role="img" aria-label="Handshake icon"></div><h4>Business and Job<br>Opportunities</h4><p class="feature-text">Our objective is to provide a comprehensive competency roadmap, instead of one.</p></div>
</section>

<section class="testimonials">
  <div class="abs" style="left:0;top:2463px;width:1200px;height:451px;background:var(--mist);z-index:-1"></div>
  <svg class="abs" style="left:0;top:2420px;z-index:-1" width="1200" height="50"><polygon points="0,43 1200,0 1200,50 0,50" fill="#f2f2f2"/></svg>
  <h2 class="section-title center abs" style="top:2502px">What People Say</h2>
  <svg class="arrow" style="left:124px" width="20" height="34" viewBox="0 0 20 34"><polyline points="17,2 3,17 17,32" fill="none" stroke="#888" stroke-width="3"/></svg>
  <svg class="arrow" style="left:1058px" width="20" height="34" viewBox="0 0 20 34"><polyline points="3,2 17,17 3,32" fill="none" stroke="#888" stroke-width="3"/></svg>
  <div class="quote" style="left:172px;top:2587px"><p>"Lorem ipsum dolor sit amet, consectet ur adipiscing elit, sed do eiusmod tempor incididunt ut labore et dolore magna aiq uaenim ad minim venia elit, sed do eiu smod tempor incididunt ut laborelor et dolore magna a enim ad minimm"</p><div class="who">- Tavin Roske<span>★★★★★</span></div><div class="mark">”</div><div class="tail"></div></div>
  <div class="quote lift" style="left:466px;top:2608px"><p>"Lorem ipsum dolor sit amet, consectet ur adipiscing elit, sed do eiusmod tempor incididunt ut labore et dolore magna aiq uaenim ad minim venia elit, sed do eiu smod tempor incididunt ut laborelor et dolore magna a enim ad minimm"</p><div class="who">- Tavin Roske<span>★★★★★</span></div><div class="mark">”</div><div class="tail"></div></div>
  <div class="quote" style="left:755px;top:2587px"><p>"Lorem ipsum dolor sit amet, consectet ur adipiscing elit, sed do eiusmod tempor incididunt ut labore et dolore magna aiq uaenim ad minim venia elit, sed do eiu smod tempor incididunt ut laborelor et dolore magna a enim ad minimm"</p><div class="who">- Tavin Roske<span>★★★★★</span></div><div class="mark">”</div><div class="tail"></div></div>
</section>

<section class="blog">
  <h2 class="section-title center abs" style="top:2984px">Latest Blog</h2>
  <p class="section-sub center" style="top:3038px">Sed ut perspiciatis unde omnise natus errort voluptatem accustiu<br>mdoloremque laedut perspictis unde omnis iste natu.</p>
  <article class="post" style="left:172px">
    <div class="post-img" role="img" aria-label="Photo of a student writing notes beside a laptop" style="background:linear-gradient(135deg,#6b3e2e,#a67a5c 55%,#d8c7b5)"></div>
    <span class="date">▣ JAN 28 2020</span>
    <h3>Lorem ipsum dolor sit alrt, conse ctetur adipiscing ld do eiusmod tem</h3>
    <p>Lorem ipsum dolor sit amet, consectetpis cing elit, sed do eiusmod tempor inc utla bore et dolore magna aliqua. Ut enimiim veniam, quis nostrud exercitatio.</p>
  </article>
  <article class="post" style="left:466px">
    <div class="post-img" role="img" aria-label="Photo of a man studying with a laptop on a sofa" style="background:linear-gradient(135deg,#c9bfae,#8d7a68 50%,#4b4f5a)"></div>
    <span class="date">▣ JAN 28 2020</span>
    <h3>Lorem ipsum dolor sit alrt, conse ctetur adipiscing ld do eiusmod tem</h3>
    <p>Lorem ipsum dolor sit amet, consectetpis cing elit, sed do eiusmod tempor inc utla bore et dolore magna aliqua. Ut enimiim veniam, quis nostrud exercitatio.</p>
  </article>
  <article class="post" style="left:761px">
    <div class="post-img" role="img" aria-label="Photo of a woman with headphones at a laptop" style="background:linear-gradient(135deg,#5a3a2c,#b38b6c 50%,#e6d9c6)"></div>
    <span class="date">▣ JAN 28 2020</span>
    <h3>Lorem ipsum dolor sit alrt, conse ctetur adipiscing ld do eiusmod tem</h3>
    <p>Lorem ipsum dolor sit amet, consectetpis cing elit, sed do eiusmod tempor inc utla bore et dolore magna aliqua. Ut enimiim veniam, quis nostrud exercitatio.</p>
  </article>
  <span class="btn btn-solid" style="left:516px;top:3591px;width:168px;height:48px">View All News</span>
</section>

<section class="news">
  <div class="abs" role="img" aria-label="Background photo of a person writing, tinted orange" style="left:0;top:3702px;width:1200px;height:369px;background:linear-gradient(100deg,#d9441c,#e8621d 50%,#f0842a)"></div>
  <svg class="abs" style="left:0;top:3702px" width="1200" height="36"><polygon points="0,0 1200,0 0,36" fill="#cfcfcf" opacity=".6"/></svg>
  <h2 class="center" style="top:3784px">Newsletter Sign up</h2>
  <p class="center" style="top:3843px">Subscribe now and receive weekly newsletter with educational materials,<br>new courses, interesting posts, popular books and much more!</p>
  <div class="email">Email:<span class="go"><svg width="31" height="31" viewBox="0 0 31 31"><polygon points="13,11 19,15.5 13,20" fill="#fff"/></svg></span></div>
</section>

<footer class="footer">
  <div class="fcol" style="left:182px">
    <h5>Contact</h5>
    <div class="contact-row"><svg width="18" height="20" viewBox="0 0 18 20"><path d="M9 1a6 6 0 0 1 6 6c0 5-6 12-6 12S3 12 3 7a6 6 0 0 1 6-6z" fill="none" stroke="#ccc" stroke-width="1.4"/><circle cx="9" cy="7" r="2" fill="none" stroke="#ccc" stroke-width="1.4"/></svg><span>418 Larkspur Way Ste 9<br>Brevard Loop, Tallow,<br>OR 97401, USA</span></div>
    <div class="contact-row"><svg width="18" height="18" viewBox="0 0 18 18"><path d="M4 1l3 4-2 2c1 2 3 4 5 5l2-2 4 3-2 3C7 16 2 11 1 4z" fill="none" stroke="#ccc" stroke-width="1.4"/></svg><span>Phone<br>+1 (800) 555 01 42</span></div>
    <div class="contact-row"><svg width="18" height="14" viewBox="0 0 18 14"><rect x="1" y="1" width="16" height="12" fill="none" stroke="#ccc" stroke-width="1.4"/><polyline points="1,1 9,8 17,1" fill="none" stroke="#ccc" stroke-width="1.4"/></svg><span>Email<br>support@study.vornaquill.com</span></div>
  </div>
  <div class="fcol" style="left:448px"><h5>About Us</h5><ul><li>Lorem ipsum dolo</li><li>Consectetur adipiscing elit.</li><li>Fusce eget leo tincid</li><li>Donec consequat</li><li>Praesent elementum</li><li>Jmauris posueret</li></ul></div>
  <div class="fcol" style="left:677px"><h5>Information</h5><ul><li>Lorem ipsum dolo</li><li>Consectetur adipiscing elit.</li><li>Fusce eec consequat</li><li>Praesent elementum</li><li>Jmauris posueret</li><li>Aenean a ex eu lectu</li></ul></div>
  <div class="fcol" style="left:890px"><h5>Other Links</h5><ul><li>Lorem ipsum dolo</li><li>Consecteturiscing elit.</li><li>Fusce eget leo tincid</li><li>Donec consequat</li><li>Praesent elementum</li><li>Aenean a ex eu lectu</li></ul></div>
  <div class="fbar"></div>
  <div class="copyright">Copyright 2020. All Rights Reserved</div>
  <div class="powered">Powered by <b>Lumora</b> <i>Courseforge</i></div>
  <div class="social" aria-label="Social links"><span></span><span></span><span></span><span></span><span></span></div>
</footer>
<div class="chat" aria-label="Chat"><svg width="22" height="20" viewBox="0 0 22 20"><rect x="1" y="1" width="20" height="14" rx="4" fill="#fff"/><polygon points="5,15 9,15 5,19" fill="#fff"/><rect x="6" y="6" width="10" height="1.6" fill="#2f7be0"/><rect x="6" y="9" width="7" height="1.6" fill="#2f7be0"/></svg></div>

</body>
</html>
```